Women's Jewellery startup needs a captivating, beautifully designed and intuitive online store

[12/24 update]

Added 2 additional documents:

Feedback on designs received so far: designer feedback.docx
Product images from catalogue: products images.docx

Please read the feedback provided on designs provided so far to guide you further on your submission. The product images can be used to create promotional banners for the site.

@@@Added a document (VELISTO JEWELLERY_checklist.docx) which can be used by designers as a checklist when submitting their designs to ensure all aspects of the requirements have been covered @@@

+++IMPORTANT BUT NOT SPECIFIED IN THE REQUIREMENTS DOCUMENT - DESIGN SHOULD INCLUDE SUPPORT FOR MOBILE FRIENDLY SITE TOO+++

***Previous experience designing Jewellery online stores preferred (not essential)***

The name of the online Jewellery store is "Velisto Jewellery" and the business is based in Hong Kong. It will be run by 2 stay at home mothers. We need a Shopify themed store designed that will achieve the following objectives in order of priority:

• Conversion: The primary objective of the design/content is to prompt the customer to make a purchase. While this may sound obvious, it is mentioned so as not to distract the design process by focusing on other objectives (which are also important). The site also needs to be optimized so as to rank high in search engine searches for relevant keywords (SEO)
• Navigation: An intuitive interface which takes away a lot of the thinking from the customer by making it obvious what they need to do when they visit the store
• Engagement: Encourages the customer to spend time on the website and share content with their social network

Where applicable, the design of the store should reflect as closely as possible the mission statements and words outlined below:

• Jewellery you’ll fall in love with
• We want every client to leave the store with a smile
• We want to be able to provide the best service we can in every situation no matter what
• We aim to increase our business by word of mouth; therefore we tell people things about our store that makes it interesting for them to share
• We love every customer, no matter how difficult things get
• We, as a team, are so well informed about our products and brands that we always have the best information for our customers
• We celebrate women here!
• We celebrate life in here!
• We celebrate beauty here!
• We celebrate families here, as jewellery often stays within families.
• We will always try to make an extra step
• We will always try to exceed the expectation of our customers
• We will go as far as we possibly can to attract a customer back to our store and connect with us
• Every client that leaves our store knows more about jewellery because we passionately told him about it
• Romantic, classic, love, warm, cool, stylish

A draft functional specification is attached with this brief. We would like the design to reflect as closely as possible the functional requirements outlined in the document. Open to suggestions to improve upon the functional requirements.

Target Market(s)

Women aged 18-55

Industry/Entity Type

Jewelry Store

Coding

Coded - Design and coding required

Number of Pages Required

5+ page

Font styles to use
Other font styles liked:
• Myriad Pro as per Logo but open to any font that complements this one

Requirements
Must have
• 1. A look that encourages the user to make a purchase
• 2. An intuitive, easy to navigate and engaging interface
• 3. Primary colour scheme as defined in the functional specification attached
• 4. Simplistic look, not too cluttered
Nice to have
• 1. Closely matching the functional requirements of the site as outlined in the requirements specification but open to any better ideas

```html
<!DOCTYPE html>
<html lang="en">
<head>
<meta charset="utf-8">
<title>Velisto Jewellery – Store Home</title>
<link href="https://fonts.googleapis.com/css2?family=Lato:ital,wght@0,400;0,700;0,900;1,400;1,700&family=Open+Sans:wght@400;600;700&display=swap" rel="stylesheet">
<style>
  :root{
    --gold:#c8952c;
    --gold-dark:#b5841f;
    --ink:#2a2a2a;
    --muted:#555;
    --line:#d9d9d9;
    --nav-dark:#2d2d2d;
    --footer:#232323;
    --footer-base:#1b1b1b;
    --card:#f2f2f2;
    --btn-grey:#5b5b5b;
    --white:#ffffff;
    --dim:rgba(0,0,0,.45);
  }
  *{box-sizing:border-box;margin:0;padding:0}
  html,body{width:1200px;height:2378px;overflow:hidden}
  body{position:relative;background:var(--white);font-family:"Open Sans",Arial,sans-serif;color:var(--ink)}
  .abs{position:absolute}

  /* announcement + utility bar */
  .announce{left:0;top:0;width:1200px;height:52px;display:flex;align-items:center;justify-content:center;font:700 15px "Lato",sans-serif;color:var(--gold)}
  .announce b{color:var(--ink)}
  .utility{left:0;top:52px;width:1200px;height:46px;background:var(--nav-dark);display:flex;align-items:center;justify-content:flex-end;padding-right:70px;gap:12px;font-size:13px;color:#ddd}
  .utility .sep{color:#888}
  .utility strong{color:#fff}

  /* header */
  .brand{left:76px;top:112px;width:240px;text-align:left}
  .brand-mark{display:flex;align-items:center;gap:10px;margin-left:38px}
  .brand-dot{width:14px;height:14px;border-radius:50%;background:var(--gold)}
  .brand-name{font:400 19px "Lato",sans-serif;letter-spacing:5px;color:var(--gold)}
  .tagline{margin-top:22px;font:italic 400 15px "Lato",sans-serif;color:var(--ink)}
  .mainnav{right:75px;top:152px;display:flex;gap:40px;font:600 14px "Open Sans",sans-serif;letter-spacing:.3px}

  /* hero */
  .hero{left:75px;top:222px;width:1050px;height:476px;background:radial-gradient(ellipse at 75% 45%,#6b4030 0%,#3a2218 30%,#141010 60%,#0b0b0b 100%)}
  .hero-title{left:178px;top:395px;font:900 58px/1.05 "Lato",sans-serif;color:#e9e9e9}
  .hero-title span{display:block;color:var(--gold)}
  .hero-arrow{width:34px;height:34px;border-radius:50%;background:#f0f0f0;display:flex;align-items:center;justify-content:center;top:443px}

  /* promo tiles */
  .promo{top:728px;width:331px;height:236px;padding:0 0 20px 16px;display:flex;flex-direction:column;justify-content:flex-end;font-family:"Lato",sans-serif}
  .promo .extra{font:700 18px "Lato",sans-serif;color:#fff}
  .promo .off,.promo .what{font:900 24px/1.15 "Lato",sans-serif;color:var(--gold)}
  .promo .till{margin-top:8px;font:italic 700 16px "Lato",sans-serif;color:#fff}
  .promo-diamond{left:75px;background:linear-gradient(135deg,#0d2230,#27495a 50%,#0f1e27)}
  .promo-ruby{left:433px;background:radial-gradient(circle at 55% 40%,#7a1420,#2a0c10 55%,#120809)}
  .promo-gold{left:794px;background:radial-gradient(circle at 70% 40%,#8b6a2e,#2b2112 50%,#050505)}

  .divider{left:75px;top:1006px;width:1050px;height:1px;background:var(--line)}
  .vdivider{left:330px;top:1040px;width:1px;height:820px;background:var(--line)}

  /* filters */
  .filters{left:75px;top:1046px;width:242px}
  .filter-head{display:flex;align-items:center;height:36px;border-bottom:1px solid var(--line);font:700 15px "Lato",sans-serif;color:var(--gold)}
  .filter-head .chev{width:14px;margin:0 18px 0 2px}
  .filter-head .toggle{margin-left:auto}
  .filter-list{list-style:none;padding:12px 0 12px 0}
  .filter-list li{display:flex;align-items:center;gap:20px;height:28.5px;font-size:13px;color:var(--ink)}
  .filter-list li::before{content:"";width:10px;height:10px;border:1.5px solid #444;border-radius:2px}
  .filter-group{margin-bottom:14px}

  /* products */
  .section-title{left:361px;top:1040px;font:600 23px "Open Sans",sans-serif}
  .sorter{right:73px;top:1040px;display:flex;align-items:center;gap:16px;font-size:13px}
  .sorter .fav{font-weight:600;color:var(--gold)}
  .sorter .select{width:128px;height:30px;border:1px solid #ccc;display:flex;align-items:center;justify-content:space-between;padding:0 10px;font-size:12px}
  .card{width:246px;height:348px;background:var(--card);text-align:center}
  .card .photo{position:absolute;left:38px;top:26px;width:170px;height:170px;border-radius:6px}
  .card .heart{position:absolute;right:14px;top:16px}
  .card .name{position:absolute;left:0;top:202px;width:100%;font-size:13.5px;line-height:1.4;padding:0 16px}
  .card .price{position:absolute;left:0;top:250px;width:100%;font:600 18px "Open Sans",sans-serif;color:var(--gold)}
  .card .actions{position:absolute;left:20px;top:286px;display:flex;gap:4px}
  .btn{height:38px;display:flex;align-items:center;justify-content:center;font:700 13px "Open Sans",sans-serif;color:#fff}
  .btn-cart{width:100px;background:var(--gold)}
  .btn-view{width:102px;background:var(--btn-grey)}
  .ph-ring{background:radial-gradient(circle,#e7d2c2,#b89378 70%,transparent 71%)}
  .ph-bracelet{background:radial-gradient(ellipse,#f4efe2,#c9b88c 65%,transparent 66%)}
  .ph-necklace{background:radial-gradient(circle,#fff 40%,#c9a45b 42%,#8a1d27 60%,transparent 62%)}
  .ph-earring{background:linear-gradient(160deg,#f2e3a8,#c79b2c 60%,#f2f2f2 61%)}
  .ph-sapphire{background:radial-gradient(circle,#1d2a66,#2c3a7a 45%,#b48a6e 60%,transparent 62%)}
  .ph-emerald{background:linear-gradient(135deg,#0b8b4a,#0e5c34)}

  .pager{left:630px;top:1826px;display:flex;gap:10px}
  .pager span{width:34px;height:34px;border:1px solid #555;display:flex;align-items:center;justify-content:center;font-size:14px}
  .pager .current{background:var(--gold);border-color:var(--gold);color:#fff}

  /* footer */
  .footer{left:0;top:1896px;width:1200px;height:264px;background:var(--footer)}
  .footer-col{top:1946px}
  .footer-col h4{font:700 17px "Lato",sans-serif;color:var(--gold);margin-bottom:12px}
  .footer-col a{display:block;font-size:13px;color:#888;text-decoration:none;line-height:26.5px}
  .news-input{left:856px;top:1981px;width:225px;height:45px;background:#f2f2f2;font-size:13px;display:flex;align-items:center;padding-left:12px}
  .news-btn{left:1081px;top:1981px;width:44px;height:45px;background:var(--gold);display:flex;align-items:center;justify-content:center}
  .social-title{left:856px;top:2052px;font:700 17px "Lato",sans-serif;color:var(--gold)}
  .social{left:856px;top:2094px;display:flex;gap:20px}
  .social span{width:20px;height:20px;border-radius:50%;background:#bbb}
  .base{left:0;top:2160px;width:1200px;height:218px;background:var(--footer-base)}
  .cards{left:468px;top:2239px;display:flex;gap:7px}
  .cards span{width:38px;height:24px;border-radius:3px;background:#d9d9d9}
  .copyright{left:0;top:2288px;width:1200px;text-align:center;font-size:12px;color:#777}

  /* newsletter modal */
  .overlay{left:0;top:0;width:1200px;height:2378px;background:var(--dim)}
  .modal{left:345px;top:203px;width:511px;height:387px;background:#fff;border:5px solid #d6d6d6}
  .modal .close{position:absolute;right:12px;top:8px;font:700 28px "Open Sans",sans-serif;color:#666}
  .modal .brand-mark{position:absolute;left:0;top:54px;width:100%;justify-content:center;margin:0}
  .modal .rule{position:absolute;left:24px;width:453px;height:1px;background:var(--line)}
  .modal h2{position:absolute;left:0;top:158px;width:100%;text-align:center;font:700 19px "Open Sans",sans-serif;letter-spacing:.4px}
  .modal .email{position:absolute;left:76px;top:214px;width:350px;height:46px;background:#ececec;display:flex;align-items:center;justify-content:center;font-size:13px}
  .modal .subscribe{position:absolute;left:76px;top:269px;width:350px;height:46px;background:var(--gold);display:flex;align-items:center;justify-content:center;font:700 15px "Open Sans",sans-serif;color:#fff;letter-spacing:.5px}
</style>
</head>
<body>

<div class="abs announce">Free shipping on all orders over&nbsp;<b>$50</b></div>

<div class="abs utility">
  <span>Sign In</span><span class="sep">/</span>
  <span>My Account</span><span class="sep">/</span>
  <span>Wishlist</span><span class="sep">/</span>
  <span>Shopping Cart</span>
  <span style="margin-left:18px">Currency: <strong>HKD</strong> ⌄</span>
  <svg width="14" height="14" viewBox="0 0 14 14" style="margin-left:22px"><circle cx="6" cy="6" r="4.5" fill="none" stroke="#ddd" stroke-width="2"/><line x1="9.5" y1="9.5" x2="13" y2="13" stroke="#ddd" stroke-width="2"/></svg>
</div>

<header>
  <div class="abs brand">
    <div class="brand-mark"><span class="brand-dot"></span><span class="brand-name">VELISTO</span></div>
    <p class="tagline">Jewellery you'll fall in love with</p>
  </div>
  <nav class="abs mainnav"><span>ABOUT US</span><span>SHOPPING</span><span>CUSTOMER CARE</span></nav>
</header>

<section>
  <div class="abs hero" role="img" aria-label="Hero banner photo of a woman wearing a diamond necklace"></div>
  <h1 class="abs hero-title">We Celebrate<span>Beauty</span></h1>
  <div class="abs hero-arrow" style="left:91px"><svg width="12" height="14" viewBox="0 0 12 14"><path d="M9 1 3 7l6 6" fill="none" stroke="#222" stroke-width="2.5"/></svg></div>
  <div class="abs hero-arrow" style="left:1075px"><svg width="12" height="14" viewBox="0 0 12 14"><path d="M3 1l6 6-6 6" fill="none" stroke="#222" stroke-width="2.5"/></svg></div>
</section>

<section>
  <div class="abs promo promo-diamond" role="img" aria-label="Promotion photo of diamond rings">
    <span class="extra">Extra</span><span class="off">10% OFF</span><span class="what">DIAMOND RINGS</span><span class="till">Till March 31st, 2018</span>
  </div>
  <div class="abs promo promo-ruby" role="img" aria-label="Promotion photo of a ruby heart pendant">
    <span class="extra">Extra</span><span class="off">10% OFF</span><span class="what">RUBY PENDANT</span><span class="till">Till March 31st, 2018</span>
  </div>
  <div class="abs promo promo-gold" role="img" aria-label="Promotion photo of a gold ring">
    <span class="extra">Extra</span><span class="off">10% OFF</span><span class="what">GOLD RINGS</span><span class="till">Till March 31st, 2018</span>
  </div>
</section>

<div class="abs divider"></div>
<div class="abs vdivider"></div>

<aside class="abs filters">
  <div class="filter-group">
    <div class="filter-head"><svg class="chev" viewBox="0 0 10 14" height="14"><path d="M2 1l6 6-6 6" fill="none" stroke="#c8952c" stroke-width="2.5"/></svg>Type<svg class="toggle" width="13" height="13"><rect x=".5" y=".5" width="12" height="12" fill="none" stroke="#444"/><line x1="3" y1="6.5" x2="10" y2="6.5" stroke="#444"/></svg></div>
    <ul class="filter-list"><li>Rings</li><li>Necklaces</li><li>Bracelets</li><li>Earring</li><li>Charms</li></ul>
  </div>
  <div class="filter-group">
    <div class="filter-head"><svg class="chev" viewBox="0 0 10 14" height="14"><path d="M2 1l6 6-6 6" fill="none" stroke="#c8952c" stroke-width="2.5"/></svg>Collection<svg class="toggle" width="13" height="13"><rect x=".5" y=".5" width="12" height="12" fill="none" stroke="#444"/><path d="M3 6.5h7M6.5 3v7" stroke="#444"/></svg></div>
    <ul class="filter-list"><li>Gold</li><li>Silver</li><li>Diamond</li><li>Ruby</li><li>Sapphire</li><li>Emerald</li><li>Moissanite</li></ul>
  </div>
  <div class="filter-group"><div class="filter-head"><svg class="chev" viewBox="0 0 10 14" height="14"><path d="M2 1l6 6-6 6" fill="none" stroke="#c8952c" stroke-width="2.5"/></svg>Metal<svg class="toggle" width="13" height="13"><rect x=".5" y=".5" width="12" height="12" fill="none" stroke="#444"/><path d="M3 6.5h7M6.5 3v7" stroke="#444"/></svg></div></div>
  <div class="filter-group"><div class="filter-head"><svg class="chev" viewBox="0 0 10 14" height="14"><path d="M2 1l6 6-6 6" fill="none" stroke="#c8952c" stroke-width="2.5"/></svg>Gemstone<svg class="toggle" width="13" height="13"><rect x=".5" y=".5" width="12" height="12" fill="none" stroke="#444"/><path d="M3 6.5h7M6.5 3v7" stroke="#444"/></svg></div></div>
  <div class="filter-group"><div class="filter-head"><svg class="chev" viewBox="0 0 10 14" height="14"><path d="M2 1l6 6-6 6" fill="none" stroke="#c8952c" stroke-width="2.5"/></svg>Price Range<svg class="toggle" width="13" height="13"><rect x=".5" y=".5" width="12" height="12" fill="none" stroke="#444"/><path d="M3 6.5h7M6.5 3v7" stroke="#444"/></svg></div></div>
</aside>

<main>
  <h2 class="abs section-title">Featured Products</h2>
  <div class="abs sorter"><span class="fav">Our Favorites</span><span class="select">What's new <span>⬍</span></span></div>

  <article class="abs card" style="left:361px;top:1094px"><div class="photo ph-ring" role="img" aria-label="Rose gold ring with emeralds"></div><svg class="heart" width="18" height="16" viewBox="0 0 18 16"><path d="M9 15 2 8a4 4 0 0 1 7-5 4 4 0 0 1 7 5z" fill="#222"/></svg><p class="name">Vestibulum ante ipsum primis in faucibus orci..</p><p class="price">$12.00</p><div class="actions"><span class="btn btn-cart">Add to Cart</span><span class="btn btn-view">Quick View</span></div></article>
  <article class="abs card" style="left:621px;top:1094px"><div class="photo ph-bracelet" role="img" aria-label="Diamond tennis bracelet"></div><svg class="heart" width="18" height="16" viewBox="0 0 18 16"><path d="M9 15 2 8a4 4 0 0 1 7-5 4 4 0 0 1 7 5z" fill="#222"/></svg><p class="name">Vestibulum ante ipsum primis in faucibus orci..</p><p class="price">$12.00</p><div class="actions"><span class="btn btn-cart">Add to Cart</span><span class="btn btn-view">Quick View</span></div></article>
  <article class="abs card" style="left:881px;top:1094px"><div class="photo ph-necklace" role="img" aria-label="Gold necklace with ruby drops"></div><svg class="heart" width="18" height="16" viewBox="0 0 18 16"><path d="M9 15 2 8a4 4 0 0 1 7-5 4 4 0 0 1 7 5z" fill="#222"/></svg><p class="name">Vestibulum ante ipsum primis in faucibus orci..</p><p class="price">$12.00</p><div class="actions"><span class="btn btn-cart">Add to Cart</span><span class="btn btn-view">Quick View</span></div></article>
  <article class="abs card" style="left:361px;top:1453px"><div class="photo ph-earring" role="img" aria-label="Gold drop earrings"></div><svg class="heart" width="18" height="16" viewBox="0 0 18 16"><path d="M9 15 2 8a4 4 0 0 1 7-5 4 4 0 0 1 7 5z" fill="#222"/></svg><p class="name">Vestibulum ante ipsum primis in faucibus orci..</p><p class="price">$12.00</p><div class="actions"><span class="btn btn-cart">Add to Cart</span><span class="btn btn-view">Quick View</span></div></article>
  <article class="abs card" style="left:621px;top:1453px"><div class="photo ph-sapphire" role="img" aria-label="Sapphire ring in rose gold"></div><svg class="heart" width="18" height="16" viewBox="0 0 18 16"><path d="M9 15 2 8a4 4 0 0 1 7-5 4 4 0 0 1 7 5z" fill="#222"/></svg><p class="name">Vestibulum ante ipsum primis in faucibus orci..</p><p class="price">$12.00</p><div class="actions"><span class="btn btn-cart">Add to Cart</span><span class="btn btn-view">Quick View</span></div></article>
  <article class="abs card" style="left:881px;top:1453px"><div class="photo ph-emerald" role="img" aria-label="Loose emerald-cut emerald gemstone"></div><svg class="heart" width="18" height="16" viewBox="0 0 18 16"><path d="M9 15 2 8a4 4 0 0 1 7-5 4 4 0 0 1 7 5z" fill="#222"/></svg><p class="name">Vestibulum ante ipsum primis in faucibus orci..</p><p class="price">$12.00</p><div class="actions"><span class="btn btn-cart">Add to Cart</span><span class="btn btn-view">Quick View</span></div></article>

  <nav class="abs pager"><span class="current">1</span><span>2</span><span>3</span><span>···</span><span>&gt;&gt;</span></nav>
</main>

<footer>
  <div class="abs footer"></div>
  <div class="abs footer-col" style="left:75px"><h4>About Us</h4><a>Our Story</a><a>Wholesale inquiries</a></div>
  <div class="abs footer-col" style="left:345px"><h4>Shopping</h4><a>Orders</a><a>Wishlist</a><a>Size Guide</a></div>
  <div class="abs footer-col" style="left:582px"><h4>Customer Care</h4><a>Returns</a><a>FAQs</a><a>Care &amp; Warranty</a><a>Contact Us</a></div>
  <div class="abs footer-col" style="left:856px"><h4>Sign Up Newsletter</h4></div>
  <div class="abs news-input">Email Address</div>
  <div class="abs news-btn"><svg width="18" height="10" viewBox="0 0 18 10"><path d="M0 5h16M12 1l4 4-4 4" fill="none" stroke="#fff" stroke-width="1.6"/></svg></div>
  <div class="abs social-title">Social Links</div>
  <div class="abs social"><span></span><span></span><span></span></div>
  <div class="abs base"></div>
  <div class="abs cards"><span></span><span></span><span></span><span></span><span></span><span></span></div>
  <p class="abs copyright">Copyright © 2017, Company Name. All Right Reserved</p>
</footer>

<div class="abs overlay"></div>
<div class="abs modal" role="dialog" aria-label="Newsletter sign-up">
  <span class="close">×</span>
  <div class="brand-mark"><span class="brand-dot"></span><span class="brand-name">VELISTO</span></div>
  <div class="rule" style="top:143px"></div>
  <h2>SIGN-UP NEWSLETTER</h2>
  <div class="rule" style="top:191px"></div>
  <div class="email">Enter Email Address</div>
  <div class="subscribe">SUBSCRIBE</div>
</div>

</body>
</html>
```